Web design for business website

I need a web design for a business website for one of our clients who is specialized in alarm management software. I would like you to design 3 web pages, one for each of the 3 pages. You need to process the corporate identity of our client to the web design. This means the colors of the logo (red and black) should definitely show up on all of the 3 pages. Find the logo file for the logo of our customer. To increase readability I suggest you use a white/light background. All suggestions are welcome.

Please kindly download atttached Webdesign.zip and read the project brief first. The project brief refers to all other files of the zip file. Your design must have exactly the same structure as the wireframes.
Updates

Target Market(s)

B2B, Alarm management

Industry/Entity Type

Business

Number of Pages Required

3 page

Requirements
Must have
• The web design must have exactly the same structure as the wireframes and needs to contain the colors of the company logo.

```html
<!DOCTYPE html>
<html lang="en">
<head>
<meta charset="utf-8">
<title>Corvexa – Real-time reasoning solutions</title>
<link href="https://fonts.googleapis.com/css2?family=Arimo:wght@400;700&display=swap" rel="stylesheet">
<style>
:root{
  --red:#c23a1f;
  --ink:#1c1a24;
  --text:#3a3a3a;
  --topbar:#e8e8e8;
  --header:#f0f0f0;
  --footer:#1b1919;
  --footer-panel:#242222;
  --footer-link:#e6e6e6;
  --line:#d9d9d9;
}
*{box-sizing:border-box;margin:0;padding:0}
html,body{width:837px;height:1200px;overflow:hidden;background:#fff;font-family:"Arimo",Arial,sans-serif;color:var(--text)}
.page{position:relative;width:837px;height:1200px}
.topbar{position:absolute;left:0;top:0;width:837px;height:32px;background:var(--topbar)}
.call{position:absolute;left:69px;top:11px;font-size:9px;font-weight:700;color:var(--ink)}
.lang{position:absolute;left:547px;top:11px;font-size:8.5px;color:var(--ink);display:flex;align-items:center;gap:4px}
.lang .flag{width:11px;height:7px;background:#2a3a8c;border:1px solid #fff;outline:1px solid #c8c8c8}
.search{position:absolute;left:623px;top:7px;width:145px;height:19px;background:#fff;border:1px solid #d6d6d6;font-size:7.5px;color:#8a8a8a;padding:5px 6px}
.header{position:absolute;left:0;top:32px;width:837px;height:120px;background:var(--header)}
.brand{position:absolute;left:69px;top:22px}
.brand .name{font-size:25px;font-weight:700;color:var(--ink);letter-spacing:1px;line-height:1}
.brand .tag{font-size:7.5px;color:var(--ink);margin-top:3px}
.userbtns{position:absolute;left:606px;top:19px;display:flex;gap:10px}
.userbtn{width:47px;height:43px;background:#fff;text-align:center;font-size:8px;color:var(--ink);padding-top:6px}
.userbtn svg{display:block;margin:0 auto 4px}
.nav{position:absolute;left:69px;top:111px;width:699px;height:41px;background:var(--red);display:flex;padding-left:22px}
.nav a{color:#fff;font-size:8.5px;text-decoration:none;line-height:41px;margin-right:45px;position:relative}
.nav a.active::after{content:"";position:absolute;left:50%;bottom:-7px;margin-left:-3px;border:3px solid transparent;border-top:4px solid var(--red)}
.hero{position:absolute;left:69px;top:167px;width:700px;height:328px;border:3px solid #fff;box-shadow:0 1px 3px rgba(0,0,0,.35),0 12px 14px -8px rgba(0,0,0,.35)}
.hero-photo{position:absolute;inset:0;background:linear-gradient(180deg,#d9a04b 0%,#e8b661 30%,#7b7a5a 55%,#3f5a33 72%,#a88a52 88%,#5b5a3b 100%)}
.hero h1{position:absolute;left:0;right:0;top:173px;text-align:center;color:#fff;font-size:29px;font-weight:700;text-shadow:0 2px 4px rgba(0,0,0,.6)}
.hero p{position:absolute;left:0;right:0;top:220px;text-align:center;color:#fff;font-size:16px;font-weight:700;text-shadow:0 2px 4px rgba(0,0,0,.6)}
.dots{position:absolute;left:335px;top:308px;display:flex;gap:2px}
.dots i{width:6px;height:6px;border-radius:50%;background:#1a1a1a}
.dots i:first-child{background:var(--red)}
.section-title{position:absolute;left:0;width:837px;text-align:center;font-size:14px;font-weight:700;color:var(--ink)}
.rule{position:absolute;height:2px;background:#bdbdbd}
.rule::before{content:"";position:absolute;left:0;top:0;width:50%;height:2px;background:var(--red)}
.rule::after{content:"";position:absolute;left:-2px;top:-2px;width:6px;height:6px;border-radius:50%;background:var(--red)}
.intro{position:absolute;left:82px;top:583px;width:674px;text-align:center;font-size:8.4px;line-height:15.6px;color:var(--text)}
.intro p+p{margin-top:12px}
.divider{position:absolute;left:69px;top:706px;width:699px;height:1px;background:var(--line)}
.clients{position:absolute;left:70px;top:803px;display:flex;gap:21px}
.client{width:81px;height:64px;border:1px solid #dcdcdc;display:flex;align-items:center;justify-content:center;font-size:10px;font-weight:700;color:#3b3b3b}
.footer{position:absolute;left:0;top:916px;width:837px;height:284px;background:var(--footer)}
.social{position:absolute;left:70px;top:21px;display:flex;gap:11px}
.social span{width:25px;height:25px;border-radius:50%;background:#2e2c2c;color:#fff;font-size:10px;font-weight:700;display:flex;align-items:center;justify-content:center}
.email{position:absolute;left:538px;top:22px;width:142px;height:23px;background:#fff;border-radius:2px;font-size:7.5px;color:#777;padding:7px 6px}
.subscribe{position:absolute;left:694px;top:22px;width:73px;height:23px;background:var(--red);color:#fff;font-size:9px;text-align:center;line-height:23px}
.footer-panel{position:absolute;left:69px;top:64px;width:699px;height:170px;background:var(--footer-panel)}
.col{position:absolute;top:34px}
.col h3{font-size:10.5px;font-weight:400;color:var(--red);margin-bottom:11px}
.col li{list-style:none;font-size:8.2px;color:var(--footer-link);line-height:18px}
.contact{font-size:8.2px;color:var(--footer-link);line-height:18px}
.contact .row{display:flex;gap:7px}
.contact svg{flex:none;margin-top:3px}
.copyright{position:absolute;left:0;top:1169px;width:837px;text-align:center;font-size:8px;color:#777}
</style>
</head>
<body>
<div class="page">
  <div class="topbar">
    <div class="call">CALL US : +31 (0) 20 555 0148</div>
    <div class="lang"><span class="flag"></span>English ▾</div>
    <div class="search">Search here...</div>
  </div>

  <header class="header">
    <div class="brand">
      <div class="name">CORVEXA</div>
      <div class="tag">Real-time reasoning solutions</div>
    </div>
    <div class="userbtns">
      <div class="userbtn"><svg width="13" height="13" viewBox="0 0 13 13"><circle cx="6.5" cy="4" r="3" fill="#2a2a2a"/><path d="M1 13c0-3.5 2.5-5 5.5-5s5.5 1.5 5.5 5z" fill="#2a2a2a"/></svg>Account</div>
      <div class="userbtn"><svg width="13" height="14" viewBox="0 0 13 14"><path d="M3.5 6V4a3 3 0 0 1 6 0v2" fill="none" stroke="#2a2a2a" stroke-width="1.6"/><rect x="1.5" y="6" width="10" height="8" fill="#2a2a2a"/></svg>Login</div>
      <div class="userbtn"><svg width="14" height="13" viewBox="0 0 14 13"><circle cx="6" cy="4" r="3" fill="#2a2a2a"/><path d="M0.5 13c0-3.5 2.5-5 5.5-5s5.5 1.5 5.5 5z" fill="#2a2a2a"/><path d="M11 2v4M9 4h4" stroke="#2a2a2a" stroke-width="1.2"/></svg>Signup</div>
    </div>
  </header>

  <nav class="nav">
    <a class="active">HOME</a><a>INDUSTRY</a><a>TELECOM</a><a>POWER</a><a>UTILITIES</a><a>INFRA</a><a>STORE</a>
  </nav>

  <section class="hero">
    <div class="hero-photo" role="img" aria-label="Refinery towers at sunset reflected in a marsh"></div>
    <h1>CORVEXA</h1>
    <p>REAL TIME REASONING SOLUTIONS</p>
    <div class="dots"><i></i><i></i><i></i><i></i></div>
  </section>

  <h2 class="section-title" style="top:529px">INTRODUCTIE CORVEXA</h2>
  <div class="rule" style="left:324px;top:562px;width:191px"></div>
  <div class="intro">
    <p>Companies have invested to get data out of processes. New technologies have been developed to getreal-time data out of the harshest places, like oil-well drill heads or the Great Barrier Riff. Data in itself means nothing without the context the data is collected in. Example: data from equipment under maintenance does not provide information to operations. Information - data which is valid and meaningful - can overwhelm any user without the proper knowledge to interpret this information.</p>
    <p>Corvexa technology enables easy application of such knowledge in a comprehensible – visual – representation and makes hypothetical reasoning with information possible<br>providing meaningful advisories to subscribers when they need it or when it is required that they are made aware of a situation which requires their attention.</p>
  </div>
  <div class="divider"></div>

  <h2 class="section-title" style="top:739px">OUR CLIENTS</h2>
  <div class="rule" style="left:352px;top:773px;width:135px"></div>
  <div class="clients">
    <div class="client">Halvern</div>
    <div class="client">Quadrix</div>
    <div class="client">Brouwmark</div>
    <div class="client">Polythane</div>
    <div class="client">Seastream</div>
    <div class="client">Duneforge</div>
    <div class="client">Conchal</div>
  </div>

  <footer class="footer">
    <div class="social"><span aria-label="Nexo">N</span><span aria-label="Pulse">P</span><span aria-label="Kinship">K</span></div>
    <div class="email">Enter your email address</div>
    <div class="subscribe">SUBSCRIBE</div>
    <div class="footer-panel">
      <div class="col" style="left:26px"><h3>SOLUTIONS</h3><ul><li>ARC Alarm Reporting</li><li>ARC Alarm Analysis</li><li>ARC Alarm Expert</li><li>USE</li></ul></div>
      <div class="col" style="left:179px"><h3>INDUSTRIES</h3><ul><li>Industry</li><li>Telecom</li><li>Power</li><li>Utilities</li><li>Infra</li></ul></div>
      <div class="col" style="left:310px"><h3>ABOUT US</h3><ul><li>Company</li><li>Overview</li><li>Leadership</li><li>Partners</li><li>Locations</li></ul></div>
      <div class="col" style="left:439px"><h3>NEWS</h3><ul><li>Product News</li><li>Partner News</li><li>Events</li><li>Press Releases</li><li>Vacancies</li></ul></div>
      <div class="col" style="left:553px"><h3>CONTACT DETAILS</h3>
        <div class="contact">
          <div class="row"><svg width="10" height="13" viewBox="0 0 10 13"><path d="M5 0a5 5 0 0 1 5 5c0 3.5-5 8-5 8S0 8.5 0 5a5 5 0 0 1 5-5z" fill="#fff"/><circle cx="5" cy="5" r="1.8" fill="#242222"/></svg><div>Northgate Ltd., 14 Harbor<br>Lane Rivertown, RT 208,<br>USA</div></div>
          <div class="row" style="margin-top:9px"><svg width="8" height="13" viewBox="0 0 8 13"><path d="M6 1C2 1 1 4 1 6.5S2 12 6 12" fill="none" stroke="#fff" stroke-width="2"/></svg><div>+31 (0) 20 555 0148</div></div>
        </div>
      </div>
    </div>
  </footer>
  <div class="copyright">Copyright @ 2015 Corvexa.All Rights Reserved.</div>
</div>
</body>
</html>
```